Full service facility management

Stationery Branding needed for Envelopes, folders, letterheads to show the services we offer (valet, security, front desk/concierge, janitorial, maintenance services to CONDOMINIUMS). We need the our logo and colors to be branded to these items

Target Market(s)

Homeowner Condominiums / High Rise residential living

Font styles to use
Sans Serif

Colors
0355a3

```html
<!DOCTYPE html>
<html lang="en">
<head>
<meta charset="utf-8">
<title>Meridian Residential Services – Stationery</title>
<link rel="stylesheet" href="https://fonts.googleapis.com/css2?family=Roboto:wght@300;400&family=Open+Sans:wght@400&display=swap">
<style>
  :root {
    --backdrop: #c3c3c3;
    --paper: #ffffff;
    --ink: #1f1d1e;
    --ink-soft: #555555;
    --paper-shadow: rgba(0,0,0,0.25);
  }
  * { margin: 0; padding: 0; box-sizing: border-box; }
  html, body { width: 1200px; height: 604px; overflow: hidden; background: var(--backdrop); }
  body { position: relative; font-family: "Roboto", sans-serif; color: var(--ink); }

  .sheet { position: absolute; background: var(--paper); box-shadow: 0 1px 3px var(--paper-shadow); }

  .brand { position: absolute; display: flex; align-items: flex-start; gap: 8px; }
  .brand-square { flex: none; border: 1.5px solid currentColor; }
  .brand-name { font-family: "Roboto", sans-serif; font-weight: 300; line-height: 1.15; }

  /* Letterhead */
  .letterhead { left: 68px; top: 75px; width: 340px; height: 462px; }
  .letterhead .brand { left: 34px; top: 37px; color: var(--ink); }
  .letterhead .brand-square { width: 29px; height: 35px; }
  .letterhead .brand-name { font-size: 8px; margin-top: 4px; }
  .contact { position: absolute; left: 239px; top: 27px; font-size: 5.6px; color: var(--ink-soft); line-height: 7.8px; font-weight: 300; }
  .contact-address { margin-bottom: 3px; }
  .contact-line { display: flex; align-items: center; gap: 4px; }
  .contact-line svg { width: 5px; height: 5px; fill: var(--ink); }
  .letter-body { position: absolute; left: 34px; top: 168px; width: 272px; font-family: "Open Sans", sans-serif; font-size: 4.7px; line-height: 9.8px; text-align: justify; color: var(--ink); }
  .signature-mark { position: absolute; left: 242px; top: 297px; width: 63px; height: 16px; background: linear-gradient(90deg, rgba(31,29,30,0.08), rgba(31,29,30,0.18)); border-radius: 2px; }
  .signature-name { position: absolute; left: 240px; top: 314px; width: 66px; text-align: right; font-size: 3.6px; color: var(--ink); }

  /* Folder */
  .folder { left: 431px; top: 75px; width: 340px; height: 462px; background: var(--ink); color: var(--paper); }
  .folder .brand { left: 46px; top: 222px; gap: 20px; }
  .folder .brand-square { width: 69px; height: 70px; border-width: 2px; }
  .folder .brand-name { font-size: 16px; margin-top: 6px; }
  .folder-url { position: absolute; left: 0; right: 0; top: 428px; text-align: center; font-size: 5.6px; letter-spacing: 0.8px; }

  /* Envelope back */
  .envelope-back { left: 794px; top: 207px; width: 334px; height: 157px; overflow: hidden; }
  .envelope-back .flap { position: absolute; left: 0; top: 0; width: 334px; height: 82px; }
  .envelope-back .flap-square { position: absolute; left: 152px; top: 26px; width: 27px; height: 27px; border: 1.2px solid var(--paper); }
  .envelope-back .flap-url { position: absolute; left: 0; right: 0; top: 56px; text-align: center; font-size: 5.4px; letter-spacing: 0.7px; color: var(--paper); }

  /* Envelope front */
  .envelope-front { left: 794px; top: 379px; width: 334px; height: 158px; }
  .envelope-front .brand { left: 20px; top: 21px; color: var(--ink); }
  .envelope-front .brand-square { width: 26px; height: 29px; }
  .envelope-front .brand-name { font-size: 7px; margin-top: 3px; }
</style>
</head>
<body>

  <section class="sheet letterhead" aria-label="Letterhead">
    <div class="brand">
      <div class="brand-square"></div>
      <div class="brand-name">Meridian<br>Residential<br>Services, Inc.</div>
    </div>

    <address class="contact" style="font-style: normal;">
      <div class="contact-address">4120 Harbor View Road<br>Juneau, Alaska 99801</div>
      <div class="contact-line"><svg viewBox="0 0 10 10"><path d="M2 0.5 L3.8 0.5 L4.4 3 L3.2 4 Q4.3 6 6 6.8 L7 5.6 L9.5 6.2 L9.5 8 Q9.5 9.5 8 9.5 Q1 9 0.5 2 Q0.5 0.5 2 0.5Z"/></svg>555-214-7730</div>
      <div class="contact-line"><svg viewBox="0 0 10 10"><rect x="2.5" y="0.5" width="5" height="3"/><rect x="0.5" y="3.5" width="9" height="4" rx="1"/><rect x="2.5" y="7" width="5" height="2.5"/></svg>555-214-7731</div>
      <div class="contact-line"><svg viewBox="0 0 10 10"><rect x="0.5" y="2" width="9" height="6.5"/><path d="M0.5 2 L5 5.5 L9.5 2" fill="none" stroke="#fff" stroke-width="0.8"/></svg>hello@meridianrs.com</div>
      <div class="contact-line"><svg viewBox="0 0 10 10"><circle cx="5" cy="5" r="4.5"/><path d="M0.5 5 H9.5 M5 0.5 V9.5" stroke="#fff" stroke-width="0.6"/></svg>www.meridianrs.com</div>
    </address>

    <p class="letter-body">Lorem ipsum dolor sit amet, consectetur adipiscing elit. Donec orci purus, luctus vitae dignissim eu, iaculis sed purus. Vivamus faucibus, ipsum nec aliquet viverra, leo mauris condimentum ligula, sit amet sagittis enim ligula quis arcu. Nam egestas tortor id nisi porttitor mattis. In tortor ante, ultricies in suscipit a, tempus non massa. Vivamus et auctor mi. Fusce vel massa nulla. Phasellus nec eros mauris, et scelerisque orci. Donec malesuada orci vitae nulla accumsan porta a id massa. Quisque accumsan iaculis magna sit amet fringilla. Maecenas consequat, magna eget tincidunt semper, odio nibh rutrum mi, id feugiat ante nisi eu risus. Vestibulum nunc orci, rhoncus a placerat in, ultricies in mi. Cras mattis varius eros, vel fringilla nisi suscipit eget.</p>

    <div class="signature-mark" role="img" aria-label="Handwritten signature"></div>
    <div class="signature-name">Dana Mercer, Manager</div>
  </section>

  <section class="sheet folder" aria-label="Presentation folder">
    <div class="brand">
      <div class="brand-square"></div>
      <div class="brand-name">Meridian<br>Residential<br>Services, Inc.</div>
    </div>
    <div class="folder-url">www.meridianrs.com</div>
  </section>

  <section class="sheet envelope-back" aria-label="Envelope back">
    <svg class="flap" viewBox="0 0 334 82" aria-hidden="true">
      <path d="M0 0 H334 V60 Q334 80 314 80 H20 Q0 80 0 60 Z" fill="var(--ink)"/>
    </svg>
    <div class="flap-square"></div>
    <div class="flap-url">www.meridianrs.com</div>
  </section>

  <section class="sheet envelope-front" aria-label="Envelope front">
    <div class="brand">
      <div class="brand-square"></div>
      <div class="brand-name">Meridian<br>Residential<br>Services, Inc.</div>
    </div>
  </section>

</body>
</html>
```